Bluecrest Learning Corps by graduating students from college in two years

Based on the logo design, create stationary and business cards for
Dr. Venrel T Oskamp, CEO, (703) 482-1736
and Marisa Deltoft, Respresentative, (301) 647-2208
Address: 4719 Pellham Court, Faurfax Station, VA 22039
Incorporate elelments of the logo

Target Market(s)

USA

Font styles to use
Other font styles liked:
• match with the logo type style

```html
<!DOCTYPE html>
<html lang="en">
<head>
<meta charset="utf-8">
<title>Bluecrest Learning Corps Letterhead</title>
<link href="https://fonts.googleapis.com/css2?family=Arimo:wght@400;700&family=Poppins:wght@600&display=swap" rel="stylesheet">
<style>
  :root {
    --navy: #14226b;
    --gold: #f5c21b;
    --ink: #4a4a4a;
    --paper: #ffffff;
    --backdrop: #e8e8e8;
  }
  * { margin: 0; padding: 0; box-sizing: border-box; }
  html, body { width: 1200px; height: 960px; overflow: hidden; }
  body {
    background: var(--backdrop);
    font-family: "Arimo", Arial, sans-serif;
    position: relative;
  }
  .letterhead {
    position: absolute;
    left: 250px; top: 27px;
    width: 700px; height: 906px;
    background: var(--paper);
    box-shadow: 0 4px 18px rgba(0,0,0,0.12);
    overflow: hidden;
  }
  .brand {
    position: absolute;
    left: 90px; top: 70px;
    display: flex; align-items: center; gap: 12px;
  }
  .brand-mark {
    width: 26px; height: 26px; border-radius: 50%;
    background: var(--gold);
  }
  .brand-name {
    font-family: "Arimo", Arial, sans-serif;
    font-weight: 700;
    font-size: 18px;
    color: var(--navy);
  }
  .letter {
    position: absolute;
    left: 90px; top: 250px;
    width: 470px;
  }
  .salutation {
    font-family: "Poppins", Arial, sans-serif;
    font-weight: 600;
    font-size: 17px;
    color: var(--ink);
    margin-bottom: 18px;
  }
  .letter p {
    font-size: 11.5px;
    line-height: 1.42;
    color: var(--ink);
    margin-bottom: 16px;
  }
  .signoff {
    font-family: "Poppins", Arial, sans-serif;
    font-weight: 600;
    font-size: 9.5px;
    color: var(--ink);
    margin-top: 28px;
  }
  .signature {
    display: block;
    margin-top: 18px;
    width: 110px; height: 30px;
    background: linear-gradient(90deg, #d9d9d9, #bdbdbd);
    border-radius: 4px;
  }
  .footer {
    position: absolute;
    left: 90px; right: 60px; bottom: 40px;
    display: flex; align-items: flex-end;
    justify-content: space-between;
  }
  .contact { color: var(--ink); font-size: 11.5px; line-height: 1.35; }
  .contact-name {
    font-weight: 700; font-size: 14px; color: var(--navy);
  }
  .contact-phone { display: flex; align-items: center; gap: 5px; }
  .contact-phone svg { width: 11px; height: 11px; fill: var(--gold); }
  .divider { width: 34px; height: 40px; margin-bottom: 6px; }
  .divider line { stroke: var(--gold); stroke-width: 1.2; }
  .address { color: var(--ink); font-size: 11.5px; line-height: 1.35; font-style: normal; }
  .edge-band {
    position: absolute; left: 0; right: 0; bottom: 0;
    height: 7px; background: var(--gold);
  }
</style>
</head>
<body>
  <main class="letterhead">
    <header class="brand">
      <span class="brand-mark"></span>
      <span class="brand-name">Bluecrest Learning Corps</span>
    </header>

    <section class="letter">
      <h1 class="salutation">Dear Mr. Smith,</h1>
      <p>Lorem ipsum dolor sit amet, consectetuer adipiscing elit, sed diam nonmmy nibh euismod tincidunt ut laor eet dolore magna aliquam erat volutpat. Ut wisi enim ad minim veniam, quis nostrud exerci tationmcorper suscipit lobortis nisl ut aliquip ex ea commodo consequat. Duis autem vel eum iriure dolor in hendrerit in vulputate velit esse molestie consequat, vel illum dolore eu feugiat</p>
      <p>Rorem ipsum dolor sit amet, consectetuer adipiscing elit, sed diam nonmmy nibh euismod tincidunt ut laor eet dolore magna aliquam erat volutpat. Ut wisi enim ad minim veniam, quis nostrud exerci tationmcorper suscipit lobortis nisl ut aliquip ex ea commodo consequat. Duis autem vel eum iriure dolor in hendrerit in vulputate velit esse molest</p>
      <p>Dorem ipsum dolor sit amet, consectetuer adipiscing elit, sed diam nonmmy nibh euismod tincidunt ut laor eet dolore magna aliquam erat volutpat. Ut wisi enim ad minim veniam, quis nostrud exerci tationmcorper suscipit lobortis nisl ut aliquip ex ea commodo consequat. Duis autem vel eum iriure dolor in hendrerit in suscipit lobortis nisl ut aliquip ex ea commodo consequat. Duis autem vel eum iriure dolor in hendrerit in vulputate velit esse molestie consequat, vel illum</p>
      <p>Sorem ipsum dolor sit amet, consectetuer adipiscing elit, sed diam nonmmy nibh euismod tincidunt ut laor eet dolore magna aliquam erat volutpat. Ut wisi enim ad minim veniam, quis nostrud exerci tationmcorper suscipit lobortis nisl ut aliquip ex ea commodo consequat. Duis autem vel eum iriure dolor in</p>
      <div class="signoff">Sincerely,</div>
      <span class="signature" role="img" aria-label="Handwritten signature"></span>
    </section>

    <footer class="footer">
      <div class="contact">
        <div class="contact-name">Dr. Venrel T Oskamp</div>
        <div>CEO</div>
        <div class="contact-phone"><svg viewBox="0 0 24 24"><path d="M6.6 10.8a15.1 15.1 0 0 0 6.6 6.6l2.2-2.2c.3-.3.7-.4 1-.2 1.1.4 2.3.6 3.6.6.6 0 1 .4 1 1V20c0 .6-.4 1-1 1A17 17 0 0 1 3 4c0-.6.4-1 1-1h3.5c.6 0 1 .4 1 1 0 1.3.2 2.5.6 3.6.1.3 0 .7-.2 1z"/></svg>(703) 482-1736</div>
      </div>
      <svg class="divider" viewBox="0 0 34 40"><line x1="2" y1="38" x2="32" y2="2"/></svg>
      <div class="contact">
        <div class="contact-name">Marisa Deltoft</div>
        <div>Respresentative</div>
        <div class="contact-phone"><svg viewBox="0 0 24 24"><path d="M6.6 10.8a15.1 15.1 0 0 0 6.6 6.6l2.2-2.2c.3-.3.7-.4 1-.2 1.1.4 2.3.6 3.6.6.6 0 1 .4 1 1V20c0 .6-.4 1-1 1A17 17 0 0 1 3 4c0-.6.4-1 1-1h3.5c.6 0 1 .4 1 1 0 1.3.2 2.5.6 3.6.1.3 0 .7-.2 1z"/></svg>(301) 647-2208</div>
      </div>
      <svg class="divider" viewBox="0 0 34 40"><line x1="2" y1="38" x2="32" y2="2"/></svg>
      <address class="address">
        4719 Pellham Court<br>Lindmoor Ridge OR 97418
      </address>
    </footer>
    <div class="edge-band"></div>
  </main>
</body>
</html>
```